Commercial Post Cards

We are looking for 3 postcards that are similar but target 3 commercial property types. they will be 6x9 cards can be front and back or not.
1. Hotel Postcard – Taviqon / Bed Bug Protection
Use the attached Taviqon sample as the primary direction.
The focus should be:
Proactive bed bug prevention and control
Protecting guests and the hotel's reputation
Regular inspections
Documentation and risk management
Professional commercial pest management
The backside should transition into our General Pest Control services, showing that we can be the hotel's complete pest management provider beyond just bed bugs.
2. Apartment Complex Postcard
Target apartment owners, property managers, and management companies.
Focus on:
General pest control
Bed bug control
Rodent control
Preventative pest management
Protecting residents and the property
Reliable, ongoing service and documentation
The message should position us as a full-service pest management partner for multifamily properties.

3. Commercial Building Postcard
Target office buildings, banks, storage facilities, and other commercial properties.

Focus on:
General commercial pest control
Rodent control
Fly management
Recurring service programs
Protecting the property, employees, customers, and reputation

Overall Direction
All three postcards should have a consistent brand and visual style, but each should feel specifically designed for its target market.

We want the messaging to communicate:
Professional • Reliable • Proactive • Locally Owned & Operated • Serving Since 2017

The goal is not to overwhelm the reader with information. These should be marketing pieces that quickly communicate the problem we solve, our expertise, and why a commercial property should contact us.

I have included some of our marketing materials for help with what we do.

```html
<!DOCTYPE html>
<html lang="en">
<head>
<meta charset="utf-8">
<title>Corvane Pest Control – Apartments/Housing Guard</title>
<link rel="stylesheet" href="https://fonts.googleapis.com/css2?family=League+Gothic&family=Open+Sans:wght@700;800&display=swap">
<style>
  :root{
    --ink:#2b2b2b;
    --red:#9b1319;
    --red-dark:#7d0f14;
    --orange:#f05a1a;
    --charcoal:#202022;
    --white:#ffffff;
    --sky:#4aa3e6;
    --lawn:#6f9a45;
  }
  *{box-sizing:border-box;margin:0;padding:0}
  html,body{width:1200px;height:800px;overflow:hidden;background:var(--white)}
  .postcard{position:relative;width:1200px;height:800px;overflow:hidden;background:var(--white);font-family:"Open Sans",Arial,sans-serif;color:var(--ink)}
  .hero-photo{position:absolute;left:380px;top:0;width:820px;height:362px;
    background:
      linear-gradient(90deg,#ffffff 0%,rgba(255,255,255,.85) 18%,rgba(255,255,255,0) 45%),
      linear-gradient(180deg,#2f8fe0 0%,#8fc6f0 30%,#e8e2d6 45%,#cfc5b5 65%,#5f8a3c 85%,#476d2c 100%);}
  .brand{position:absolute;left:40px;top:62px;display:flex;align-items:center;gap:12px}
  .brand-mark{width:34px;height:34px;background:var(--orange)}
  .brand-name{font-family:"Open Sans",Arial,sans-serif;font-weight:800;font-size:34px;color:var(--ink);letter-spacing:-.5px}
  .headline{position:absolute;left:38px;top:148px;font-family:"League Gothic",Impact,sans-serif;line-height:.86;text-transform:uppercase}
  .headline .line-dark{display:block;font-size:80px;color:var(--ink);letter-spacing:2.5px}
  .headline .line-red{display:block;font-size:80px;color:var(--red);letter-spacing:2px}
  .subhead{position:absolute;left:39px;top:294px;font-size:23px;line-height:29px;font-weight:700;color:var(--ink)}
  .promise-band{position:absolute;left:0;top:360px;width:1200px;height:53px;background:var(--red);border-bottom:5px solid var(--charcoal);height:58px}
  .promise-text{position:absolute;left:118px;top:375px;font-size:16.5px;font-weight:700;color:var(--white);white-space:nowrap}
  .promise-shield{position:absolute;left:38px;top:348px;width:72px;height:78px}
  .callout{position:absolute;left:36px;top:452px;font-family:"League Gothic",Impact,sans-serif;line-height:.86;text-transform:uppercase}
  .callout .line-dark{display:block;font-size:106px;color:var(--ink);letter-spacing:1px}
  .callout .line-red{display:block;font-size:106px;color:var(--red);letter-spacing:1px}
  .service-list{position:absolute;list-style:none;font-size:20.5px;font-weight:700;line-height:25px;color:var(--ink)}
  .service-list li{position:relative;padding-left:44px;margin-bottom:15px}
  .service-list svg{position:absolute;left:0;top:1px;width:24px;height:26px}
  .services-a{left:617px;top:457px;width:290px}
  .services-b{left:908px;top:457px;width:270px}
  .footer{position:absolute;left:0;top:685px;width:1200px;height:115px;background:var(--charcoal)}
  .cta{position:absolute;left:250px;top:667px;width:733px;height:48px;background:var(--red);border-radius:0 24px 24px 0}
  .cta-light{position:absolute;left:670px;top:671px;width:309px;height:40px;background:var(--white);border-radius:0 20px 20px 0;clip-path:polygon(0 0,100% 0,100% 100%,0 100%,20px 50%)}
  .cta-text{position:absolute;top:677px;font-size:22.5px;font-weight:700;white-space:nowrap;text-transform:uppercase}
  .cta-text.ask{left:298px;color:var(--white)}
  .cta-text.property{left:700px;color:var(--ink)}
  .cta-shield{position:absolute;left:218px;top:646px;width:74px;height:84px}
  .contact{position:absolute;top:733px;display:flex;align-items:center;gap:20px;color:var(--white);font-size:32px;font-weight:700;white-space:nowrap}
  .contact svg{width:28px;height:28px}
  .contact.phone{left:292px}
  .contact.web{left:641px}
  .divider{position:absolute;left:599px;top:732px;width:2px;height:46px;background:var(--white)}
</style>
</head>
<body>
<main class="postcard">
  <div class="hero-photo" role="img" aria-label="Sunny photo of modern white multi-storey apartment buildings with glass balconies, trees and landscaped lawns under a blue sky"></div>

  <div class="brand">
    <span class="brand-mark"></span>
    <span class="brand-name">Corvane Pest Control</span>
  </div>

  <h1 class="headline"><span class="line-dark">Apartments/Housing</span><span class="line-red">Guard</span></h1>
  <p class="subhead">Proactive Pest Management for<br>Apartments &amp; Housing Communities</p>

  <div class="promise-band"></div>
  <svg class="promise-shield" viewBox="0 0 72 78" aria-hidden="true">
    <path d="M36 2 L68 14 L64 48 Q58 66 36 76 Q14 66 8 48 L4 14 Z" fill="var(--orange)"/>
    <path d="M36 8 L62 18 L58 47 Q53 61 36 70 Q19 61 14 47 L10 18 Z" fill="var(--white)"/>
    <path d="M24 38 L33 47 L49 29" fill="none" stroke="var(--ink)" stroke-width="6" stroke-linecap="round" stroke-linejoin="round"/>
  </svg>
  <p class="promise-text">Proactive protection. Quarterly inspected. Documented results. Peace of mind for your residents and your property.</p>

  <h2 class="callout"><span class="line-dark">Don’t let pests</span><span class="line-red">move in.</span></h2>

  <svg width="0" height="0" style="position:absolute" aria-hidden="true">
    <symbol id="tick-shield" viewBox="0 0 24 26">
      <path d="M12 1 L23 5 L22 15 Q20 22 12 25 Q4 22 2 15 L1 5 Z" fill="var(--red)"/>
      <path d="M12 4 L20 7 L19 15 Q17 20 12 22 Q7 20 5 15 L4 7 Z" fill="var(--ink)"/>
      <path d="M8 13 L11 16 L16 10" fill="none" stroke="var(--white)" stroke-width="2.2" stroke-linecap="round" stroke-linejoin="round"/>
    </symbol>
  </svg>

  <ul class="service-list services-a">
    <li><svg><use href="#tick-shield"/></svg>General pest control</li>
    <li><svg><use href="#tick-shield"/></svg>Bed bug control</li>
    <li><svg><use href="#tick-shield"/></svg>Rodent control</li>
    <li><svg><use href="#tick-shield"/></svg>Preventative pest management</li>
  </ul>
  <ul class="service-list services-b">
    <li><svg><use href="#tick-shield"/></svg>Protecting residents and the property</li>
    <li><svg><use href="#tick-shield"/></svg>Reliable, ongoing service and documentation</li>
  </ul>

  <div class="footer"></div>
  <div class="cta"></div>
  <div class="cta-light"></div>
  <svg class="cta-shield" viewBox="0 0 74 84" aria-hidden="true">
    <path d="M37 2 L70 14 L67 50 Q60 70 37 82 Q14 70 7 50 L4 14 Z" fill="var(--red)"/>
    <path d="M37 9 L63 19 L60 49 Q55 64 37 74 Q19 64 14 49 L11 19 Z" fill="var(--white)"/>
    <path d="M37 14 L58 22 L56 48 Q51 60 37 68 Q23 60 18 48 L16 22 Z" fill="var(--ink)"/>
    <rect x="22" y="28" width="20" height="15" rx="3" fill="var(--white)"/>
    <path d="M26 43 L24 49 L31 43 Z" fill="var(--white)"/>
    <rect x="33" y="36" width="20" height="14" rx="3" fill="var(--white)" stroke="var(--ink)" stroke-width="2"/>
    <text x="32" y="40" font-family="Open Sans, sans-serif" font-size="11" font-weight="800" fill="var(--ink)" text-anchor="middle">?</text>
  </svg>
  <span class="cta-text ask">Ask us for a custom quote</span>
  <span class="cta-text property">For your property.</span>

  <div class="contact phone">
    <svg viewBox="0 0 28 28" aria-hidden="true"><circle cx="14" cy="14" r="14" fill="var(--red)"/><path d="M9 7 Q7 8 8 12 Q11 19 17 21 Q20 22 21 19 L18 16 L16 17 Q13 15 12 12 L13 10 Z" fill="var(--white)"/></svg>
    <span>208-555-0173</span>
  </div>
  <div class="divider"></div>
  <div class="contact web">
    <svg viewBox="0 0 28 28" aria-hidden="true"><circle cx="14" cy="14" r="14" fill="var(--red)"/><path d="M20 8 L7 13 L13 15 L15 21 Z" fill="var(--white)"/></svg>
    <span>www.corvanepest.com</span>
  </div>
</main>
</body>
</html>
```